TLK Electricial Contracting Services

Hi guys, after a design for my small electrical company, have logo design files to be incorporated into the layout, the basic concept is electrical contracting services for residential, commercial, industrial & data services, image is clean clear and strong,

Card format is to have a nice clean logo on front,with maybe the Residential – commercial – industrial - data, followed with licensed & insured, followed by contact details on backside of the card.

Target Market(s)

Residential, commercial, industrial sectors.

Industry/Entity Type

Electrical

Contact Information for Business Card

TLK logo,
Residential – commercial – industrial - data
REC: 61307
Email: tlk@vornamail.net.au
Phone: 0487 352 019

Requirements
Must have
• Clean & strong design.
Nice to have
• If possible, I would like the logo colours inverted so the text is orange and the background is black on the front of the card, then the backside of the card be the reverse colour
Should not have
• No Sparks, lightning bolts,

```html
<!DOCTYPE html>
<html lang="en">
<head>
<meta charset="utf-8">
<title>TLK Electrical – Business Card</title>
<link href="https://fonts.googleapis.com/css2?family=Open+Sans:wght@400;700;800&display=swap" rel="stylesheet">
<style>
  :root {
    --bg: #e9e9e9;
    --black: #050505;
    --orange: #f5822e;
    --grey-text: #8a8a8a;
    --divider: #1a1a1a;
  }
  * { margin: 0; padding: 0; box-sizing: border-box; }
  html, body {
    width: 1200px; height: 1000px; overflow: hidden;
    background: var(--bg);
    font-family: "Open Sans", Arial, sans-serif;
  }
  .stage { position: relative; width: 1200px; height: 1000px; }

  .card {
    position: absolute;
    width: 700px; height: 400px;
    left: 250px;
    background: var(--black);
    overflow: hidden;
    box-shadow: 0 6px 18px rgba(0,0,0,0.25);
  }
  .card--back { top: 60px; }
  .card--front { top: 540px; }

  /* Back side */
  .back-stripes {
    position: absolute; left: 0; top: 0;
    width: 48%; height: 100%;
    display: flex; flex-direction: column; gap: 8px;
    background: var(--divider);
  }
  .back-stripes span { flex: 1; background: var(--orange); }
  .back-brand {
    position: absolute; left: 52%; right: 0; top: 0; bottom: 0;
    display: flex; flex-direction: column; justify-content: center; align-items: center;
    color: var(--orange); font-weight: 800;
  }
  .back-brand .brand-mark { font-size: 96px; line-height: 1; letter-spacing: 2px; }
  .back-brand .brand-name { font-size: 20px; margin-top: 4px; }

  /* Front side */
  .front-brand {
    position: absolute; left: 70px; top: 36px;
    color: var(--orange); font-weight: 800;
  }
  .front-brand .brand-mark { font-size: 80px; line-height: 1; letter-spacing: 2px; }
  .front-brand .brand-name { font-size: 17px; margin-top: 2px; }
  .glow-line {
    position: absolute; left: 270px; right: 0; top: 102px; height: 7px;
    background: var(--orange);
    box-shadow: 0 0 10px rgba(245,130,46,0.8);
  }
  .services, .credentials {
    position: absolute; left: 70px;
    color: var(--grey-text); font-size: 15px; letter-spacing: 0.5px;
  }
  .services { top: 152px; }
  .credentials { top: 176px; }
  .contact {
    position: absolute; left: 70px; top: 210px;
    list-style: none; color: var(--grey-text);
    font-size: 16px; letter-spacing: 1px;
  }
  .contact li { display: flex; align-items: center; gap: 14px; margin-bottom: 5px; line-height: 22px; }
  .contact svg { width: 12px; height: 12px; }
  .front-band {
    position: absolute; left: 0; right: 0; bottom: 0; height: 72px;
    background: var(--orange);
  }
</style>
</head>
<body>
<main class="stage">
  <section class="card card--back" aria-label="Business card back">
    <div class="back-stripes"><span></span><span></span><span></span></div>
    <div class="back-brand">
      <div class="brand-mark">TLK</div>
      <div class="brand-name">TLK Electrical</div>
    </div>
  </section>

  <section class="card card--front" aria-label="Business card front">
    <div class="front-brand">
      <div class="brand-mark">TLK</div>
      <div class="brand-name">TLK Electrical</div>
    </div>
    <div class="glow-line"></div>
    <p class="services">Residential - Commercial - Industrial - Data</p>
    <p class="credentials">Licensed &amp; Insured</p>
    <ul class="contact">
      <li>
        <svg viewBox="0 0 12 12"><polyline points="3,2 8,6 3,10" fill="none" stroke="#f5822e" stroke-width="2"/></svg>
        <span>REC: 61307</span>
      </li>
      <li>
        <svg viewBox="0 0 12 12"><polyline points="3,2 8,6 3,10" fill="none" stroke="#f5822e" stroke-width="2"/></svg>
        <span>0487-352-019</span>
      </li>
      <li>
        <svg viewBox="0 0 12 12"><polyline points="3,2 8,6 3,10" fill="none" stroke="#f5822e" stroke-width="2"/></svg>
        <span>tlk@vornamail.net.au</span>
      </li>
    </ul>
    <div class="front-band"></div>
  </section>
</main>
</body>
</html>
```